Mortgage Company ready to make a statement!

We have a basic logo that I am fairly happy with ... but it could use a little bit of tweaking before we order the sign for our building. We also want some knock-your-socks-off business cards.
Problem: Inside of our Mortgage Office (Bright Fern Mortgage Group), we are going to have a coffee lounge (Sunbrew Cafe) for Realtors to use instead of the local Cuppington to meet with homebuyers. The office and coffee lounge are in an industrial building and is decorated with cozy overstuffed chairs, a hodge podge of interesting lamps and furniture, and goal is to make it as inviting as possible. However, we are a financial institution... so we need to keep it pretty clean as well.
One of my favorite marketing ideas is to cut a house key for everyone who buys a home using us with a key that matches our logo. There's only one key shape that works really well, so that needs to match the logo in order for the idea to work. I'll attach an image of the key blank.... although the way the key hole cut out looks terrible, so I was thinking of having them just do a thin outline instead.
Would like a similar, matching logo for the Sunbrew Cafe... but possibly something that would be a little less formal and would be cute on a coffee mug- nothing stuffy.
AND, we're opening a home inspection company as well, and we would like that logo and branding to match. The home inspection company is "Bright Fern Home Inspections"
We were thinking that for the home inspection company , we could use a magnifying glass shape inside of the house shape for the logo, use a keyhole shape inside of the same house for the mortgage company, and use a coffee cup inside of the house shape for Sunbrew Cafe.
Just getting stuck and need to help. I designed the attached logo myself, and that is what we are currently using. Designers at local printing companies have failed to impress us.
The mortgage industry has a lot of numbers and logos, etc that they require us to put on our business cards... so it's hard to keep them looking clean.
HELP! HELP! :)

```html
<!DOCTYPE html>
<html lang="en">
<head>
<meta charset="utf-8">
<title>Bright Fern Mortgage Group – Business Card</title>
<link href="https://fonts.googleapis.com/css2?family=Alegreya:wght@700&family=Source+Sans+3:wght@400;600&display=swap" rel="stylesheet">
<style>
  :root {
    --backdrop: #1b1b1b;
    --card-light: #f2f2f2;
    --card-blue: #23637f;
    --brand-blue: #1f5f80;
    --ink: #1a1a1a;
    --white: #ffffff;
  }
  * { margin: 0; padding: 0; box-sizing: border-box; }
  html, body {
    width: 1200px; height: 900px; overflow: hidden;
    background: var(--backdrop);
    font-family: "Source Sans 3", Arial, sans-serif;
  }
  .stage { position: relative; width: 1200px; height: 900px; }
  .card {
    position: absolute; top: 170px;
    width: 347px; height: 561px;
  }
  .card--front { left: 259px; background: var(--card-light); }
  .card--back { left: 631px; background: var(--card-blue); }

  .brand {
    position: absolute; left: 0; right: 0;
    display: flex; align-items: center; justify-content: center; gap: 12px;
    font-family: "Source Sans 3", Arial, sans-serif;
    font-weight: 400; font-size: 27px; line-height: 1.1;
    letter-spacing: 0.5px;
  }
  .brand__mark { width: 30px; height: 30px; flex: none; }
  .card--front .brand { top: 132px; color: var(--brand-blue); }
  .card--front .brand__mark { background: var(--brand-blue); }
  .card--back .brand { top: 252px; color: var(--white); }
  .card--back .brand__mark { background: var(--white); }

  .contact {
    position: absolute; top: 320px; left: 0; right: 0;
    text-align: center; color: var(--ink); font-size: 15px;
  }
  .contact__name {
    font-family: "Alegreya", Georgia, serif; font-weight: 700;
    font-size: 22px; color: var(--brand-blue); letter-spacing: 0.5px;
    line-height: 26px;
  }
  .contact__title { line-height: 20px; }
  .contact__rule {
    width: 116px; height: 1px; background: var(--brand-blue);
    margin: 18px auto 16px;
  }
  .contact__line { line-height: 21px; }
  .contact__label { font-weight: 600; color: var(--brand-blue); }
  .contact__phone { color: var(--brand-blue); }
  .contact__web { font-weight: 600; }
  .contact__web span { color: var(--brand-blue); }
  .contact__address { margin-top: 12px; line-height: 17px; }
</style>
</head>
<body>
<main class="stage">
  <section class="card card--front">
    <div class="brand">
      <span class="brand__mark"></span>
      <span class="brand__name">Bright Fern<br>Mortgage Group</span>
    </div>
    <div class="contact">
      <div class="contact__name">EVAN CARTER</div>
      <div class="contact__title">Managing Director</div>
      <div class="contact__rule"></div>
      <div class="contact__line"><span class="contact__label">P:</span> <span class="contact__phone">823-555-0142</span></div>
      <div class="contact__line"><span class="contact__label">E:</span> hello@brightfernmail.com</div>
      <div class="contact__line contact__web"><span>www.</span>brightfernmortgage<span>.com</span></div>
      <div class="contact__address">1234, Address Goes Here<br>Country Name, 123456</div>
    </div>
  </section>

  <section class="card card--back">
    <div class="brand">
      <span class="brand__mark"></span>
      <span class="brand__name">Bright Fern<br>Mortgage Group</span>
    </div>
  </section>
</main>
</body>
</html>
```